Step and Repeat Backdrop for wedding reception photo booth

Would like to have a Step and Repeat Backdrop (8 foot high by 10 foot wide) that incorporates the wedding logo (attached) and the names Helen and Gavin. Background should be white, and wedding colors are burgundy and gold. Show me creativity :-) I have included some random samples.

```html
<!DOCTYPE html>
<html lang="en">
<head>
<meta charset="utf-8">
<title>Helen &amp; Gavin — Step and Repeat Backdrop</title>
<link rel="stylesheet" href="https://fonts.googleapis.com/css2?family=Playfair+Display:wght@500&display=swap">
<style>
  :root {
    --page: #e9e7e4;
    --backdrop: #ffffff;
    --burgundy: #7a1f2b;
    --gold: #c9a13b;
    --gold-soft: rgba(201, 161, 59, 0.65);
    --gold-faint: rgba(201, 161, 59, 0.2);
    --serif: "Playfair Display", Georgia, serif;
  }
  * { box-sizing: border-box; margin: 0; padding: 0; }
  html, body {
    width: 1200px; height: 600px; overflow: hidden;
    background: var(--page);
  }
  .stage {
    position: relative; width: 1200px; height: 600px;
    display: flex; align-items: center; justify-content: center;
  }
  .backdrop {
    position: relative; width: 750px; height: 600px;
    background: var(--backdrop);
    overflow: hidden;
  }
  .mark {
    position: absolute;
    left: var(--x); top: var(--y);
    transform: translate(-50%, -50%);
    width: 76px;
    display: flex; flex-direction: column; align-items: center; gap: 4px;
  }
  .mark-ornament {
    width: 60px; height: 10px; border-radius: 5px;
    background: radial-gradient(ellipse at center, var(--gold-soft), var(--gold-faint) 70%, transparent);
  }
  .mark-initials {
    font-family: var(--serif); font-weight: 500;
    font-size: 27px; line-height: 1; color: var(--burgundy);
    letter-spacing: -1px;
  }
  .feature {
    position: absolute; left: 374px; top: 300px;
    transform: translate(-50%, -50%);
    width: 290px;
    display: flex; flex-direction: column; align-items: center; gap: 16px;
  }
  .feature-ornament {
    width: 280px; height: 76px; border-radius: 38px;
    background: radial-gradient(ellipse at center, var(--gold-soft), var(--gold-faint) 65%, transparent);
  }
  .feature-initials {
    font-family: var(--serif); font-weight: 500;
    font-size: 104px; line-height: 1; color: var(--burgundy);
    letter-spacing: -4px;
  }
</style>
</head>
<body>
<main class="stage">
  <section class="backdrop" aria-label="Helen and Gavin wedding step and repeat backdrop">

    <div class="feature">
      <div class="feature-ornament" role="img" aria-label="Gold scrollwork flourish with fleur-de-lis above the monogram"></div>
      <div class="feature-initials">H&amp;G</div>
      <div class="feature-ornament" role="img" aria-label="Gold scrollwork flourish with fleur-de-lis below the monogram"></div>
    </div>

    <div class="mark" style="--x:37px;--y:-20px"><div class="mark-ornament" role="img" aria-label="Small gold flourish"></div><div class="mark-initials">H&amp;G</div><div class="mark-ornament" role="img" aria-label="Small gold flourish"></div></div>
    <div class="mark" style="--x:262px;--y:-20px"><div class="mark-ornament" role="img" aria-label="Small gold flourish"></div><div class="mark-initials">H&amp;G</div><div class="mark-ornament" role="img" aria-label="Small gold flourish"></div></div>
    <div class="mark" style="--x:487px;--y:-20px"><div class="mark-ornament" role="img" aria-label="Small gold flourish"></div><div class="mark-initials">H&amp;G</div><div class="mark-ornament" role="img" aria-label="Small gold flourish"></div></div>
    <div class="mark" style="--x:711px;--y:-20px"><div class="mark-ornament" role="img" aria-label="Small gold flourish"></div><div class="mark-initials">H&amp;G</div><div class="mark-ornament" role="img" aria-label="Small gold flourish"></div></div>

    <div class="mark" style="--x:149px;--y:45px"><div class="mark-ornament" role="img" aria-label="Small gold flourish"></div><div class="mark-initials">H&amp;G</div><div class="mark-ornament" role="img" aria-label="Small gold flourish"></div></div>
    <div class="mark" style="--x:375px;--y:45px"><div class="mark-ornament" role="img" aria-label="Small gold flourish"></div><div class="mark-initials">H&amp;G</div><div class="mark-ornament" role="img" aria-label="Small gold flourish"></div></div>
    <div class="mark" style="--x:600px;--y:45px"><div class="mark-ornament" role="img" aria-label="Small gold flourish"></div><div class="mark-initials">H&amp;G</div><div class="mark-ornament" role="img" aria-label="Small gold flourish"></div></div>

    <div class="mark" style="--x:37px;--y:110px"><div class="mark-ornament" role="img" aria-label="Small gold flourish"></div><div class="mark-initials">H&amp;G</div><div class="mark-ornament" role="img" aria-label="Small gold flourish"></div></div>
    <div class="mark" style="--x:262px;--y:110px"><div class="mark-ornament" role="img" aria-label="Small gold flourish"></div><div class="mark-initials">H&amp;G</div><div class="mark-ornament" role="img" aria-label="Small gold flourish"></div></div>
    <div class="mark" style="--x:487px;--y:110px"><div class="mark-ornament" role="img" aria-label="Small gold flourish"></div><div class="mark-initials">H&amp;G</div><div class="mark-ornament" role="img" aria-label="Small gold flourish"></div></div>
    <div class="mark" style="--x:711px;--y:110px"><div class="mark-ornament" role="img" aria-label="Small gold flourish"></div><div class="mark-initials">H&amp;G</div><div class="mark-ornament" role="img" aria-label="Small gold flourish"></div></div>

    <div class="mark" style="--x:149px;--y:170px"><div class="mark-ornament" role="img" aria-label="Small gold flourish"></div><div class="mark-initials">H&amp;G</div><div class="mark-ornament" role="img" aria-label="Small gold flourish"></div></div>
    <div class="mark" style="--x:600px;--y:170px"><div class="mark-ornament" role="img" aria-label="Small gold flourish"></div><div class="mark-initials">H&amp;G</div><div class="mark-ornament" role="img" aria-label="Small gold flourish"></div></div>

    <div class="mark" style="--x:37px;--y:235px"><div class="mark-ornament" role="img" aria-label="Small gold flourish"></div><div class="mark-initials">H&amp;G</div><div class="mark-ornament" role="img" aria-label="Small gold flourish"></div></div>
    <div class="mark" style="--x:711px;--y:235px"><div class="mark-ornament" role="img" aria-label="Small gold flourish"></div><div class="mark-initials">H&amp;G</div><div class="mark-ornament" role="img" aria-label="Small gold flourish"></div></div>

    <div class="mark" style="--x:149px;--y:297px"><div class="mark-ornament" role="img" aria-label="Small gold flourish"></div><div class="mark-initials">H&amp;G</div><div class="mark-ornament" role="img" aria-label="Small gold flourish"></div></div>
    <div class="mark" style="--x:600px;--y:297px"><div class="mark-ornament" role="img" aria-label="Small gold flourish"></div><div class="mark-initials">H&amp;G</div><div class="mark-ornament" role="img" aria-label="Small gold flourish"></div></div>

    <div class="mark" style="--x:37px;--y:360px"><div class="mark-ornament" role="img" aria-label="Small gold flourish"></div><div class="mark-initials">H&amp;G</div><div class="mark-ornament" role="img" aria-label="Small gold flourish"></div></div>
    <div class="mark" style="--x:711px;--y:360px"><div class="mark-ornament" role="img" aria-label="Small gold flourish"></div><div class="mark-initials">H&amp;G</div><div class="mark-ornament" role="img" aria-label="Small gold flourish"></div></div>

    <div class="mark" style="--x:149px;--y:424px"><div class="mark-ornament" role="img" aria-label="Small gold flourish"></div><div class="mark-initials">H&amp;G</div><div class="mark-ornament" role="img" aria-label="Small gold flourish"></div></div>
    <div class="mark" style="--x:600px;--y:424px"><div class="mark-ornament" role="img" aria-label="Small gold flourish"></div><div class="mark-initials">H&amp;G</div><div class="mark-ornament" role="img" aria-label="Small gold flourish"></div></div>

    <div class="mark" style="--x:37px;--y:487px"><div class="mark-ornament" role="img" aria-label="Small gold flourish"></div><div class="mark-initials">H&amp;G</div><div class="mark-ornament" role="img" aria-label="Small gold flourish"></div></div>
    <div class="mark" style="--x:262px;--y:487px"><div class="mark-ornament" role="img" aria-label="Small gold flourish"></div><div class="mark-initials">H&amp;G</div><div class="mark-ornament" role="img" aria-label="Small gold flourish"></div></div>
    <div class="mark" style="--x:487px;--y:487px"><div class="mark-ornament" role="img" aria-label="Small gold flourish"></div><div class="mark-initials">H&amp;G</div><div class="mark-ornament" role="img" aria-label="Small gold flourish"></div></div>
    <div class="mark" style="--x:711px;--y:487px"><div class="mark-ornament" role="img" aria-label="Small gold flourish"></div><div class="mark-initials">H&amp;G</div><div class="mark-ornament" role="img" aria-label="Small gold flourish"></div></div>

    <div class="mark" style="--x:149px;--y:552px"><div class="mark-ornament" role="img" aria-label="Small gold flourish"></div><div class="mark-initials">H&amp;G</div><div class="mark-ornament" role="img" aria-label="Small gold flourish"></div></div>
    <div class="mark" style="--x:375px;--y:552px"><div class="mark-ornament" role="img" aria-label="Small gold flourish"></div><div class="mark-initials">H&amp;G</div><div class="mark-ornament" role="img" aria-label="Small gold flourish"></div></div>
    <div class="mark" style="--x:600px;--y:552px"><div class="mark-ornament" role="img" aria-label="Small gold flourish"></div><div class="mark-initials">H&amp;G</div><div class="mark-ornament" role="img" aria-label="Small gold flourish"></div></div>

    <div class="mark" style="--x:37px;--y:617px"><div class="mark-ornament" role="img" aria-label="Small gold flourish"></div><div class="mark-initials">H&amp;G</div><div class="mark-ornament" role="img" aria-label="Small gold flourish"></div></div>
    <div class="mark" style="--x:262px;--y:617px"><div class="mark-ornament" role="img" aria-label="Small gold flourish"></div><div class="mark-initials">H&amp;G</div><div class="mark-ornament" role="img" aria-label="Small gold flourish"></div></div>
    <div class="mark" style="--x:487px;--y:617px"><div class="mark-ornament" role="img" aria-label="Small gold flourish"></div><div class="mark-initials">H&amp;G</div><div class="mark-ornament" role="img" aria-label="Small gold flourish"></div></div>
    <div class="mark" style="--x:711px;--y:617px"><div class="mark-ornament" role="img" aria-label="Small gold flourish"></div><div class="mark-initials">H&amp;G</div><div class="mark-ornament" role="img" aria-label="Small gold flourish"></div></div>

  </section>
</main>
</body>
</html>
```